BOLD & MINIMALIST DESIGN NEEDED

We want a very bold but minimalistic business card design that is impactful and utilizes both sides of the business card. Our current logo is included for your use.

We want bold fonts and good use of negative space. We don't want the logo to overpower the design.

Target Market(s)

Professionals who are building new commercial buildings.

Industry/Entity Type

Construction

Contact Information for Business Card

Name, Title, email, office phone, cell phone, website

Font styles to use
Serif
Sans Serif

Requirements
Must have
• Bold design!

```html
<!DOCTYPE html>
<html lang="en">
<head>
<meta charset="utf-8">
<title>Ridgeline Design + Build – Business Card</title>
<link rel="stylesheet" href="https://fonts.googleapis.com/css2?family=Oswald:wght@600&family=Montserrat:wght@400&display=swap">
<style>
  :root {
    --page-bg: #d9d2c7;
    --card-face: #f1f0ec;
    --band-dark: #262424;
    --accent-green: #7cc520;
    --ink-dark: #1b1b1b;
    --ink-light: #c9c9c9;
    --divider: #e9e9e6;
  }
  * { margin: 0; padding: 0; box-sizing: border-box; }
  html, body {
    width: 1200px; height: 887px; overflow: hidden;
    background: var(--page-bg);
  }
  .stage {
    position: relative; width: 1200px; height: 887px;
  }
  .card {
    position: absolute; left: 100px; top: 158px;
    width: 1000px; height: 571px;
    border-radius: 24px; overflow: hidden;
    background: var(--card-face);
    box-shadow: 0 18px 40px rgba(0,0,0,0.18);
  }
  .card-bands {
    position: absolute; inset: 0; width: 100%; height: 100%;
  }
  .holder-name {
    position: absolute; left: 64px; top: 52px;
    font-family: "Oswald", sans-serif; font-weight: 600;
    font-size: 48px; letter-spacing: 0.5px; line-height: 1;
    color: var(--accent-green); text-transform: uppercase;
  }
  .holder-title {
    position: absolute; left: 63px; top: 110px;
    font-family: "Montserrat", sans-serif; font-weight: 400;
    font-size: 20px; letter-spacing: 1.5px;
    color: var(--ink-dark);
  }
  .brand {
    position: absolute; right: 60px; top: 200px;
    display: flex; align-items: center; gap: 14px;
    font-family: "Montserrat", sans-serif; font-weight: 400;
    font-size: 30px; line-height: 1;
    color: var(--ink-dark); white-space: nowrap;
  }
  .brand-mark {
    width: 26px; height: 26px; flex: none;
    background: var(--ink-dark);
  }
  .contact-list {
    position: absolute; left: 58px; top: 397px;
    list-style: none;
    font-family: "Montserrat", sans-serif; font-weight: 400;
    font-size: 22px; color: var(--ink-light);
  }
  .contact-item {
    display: flex; align-items: center; height: 30.5px;
  }
  .contact-icon {
    width: 22px; height: 22px; margin-right: 10px; flex: none;
  }
  .contact-highlight { color: var(--accent-green); }
</style>
</head>
<body>
<main class="stage">
  <section class="card" aria-label="Business card front">
    <svg class="card-bands" viewBox="0 0 1000 571" preserveAspectRatio="none" aria-hidden="true">
      <path d="M150 262 C 420 392, 700 402, 1000 382 L1000 412 C 680 426, 400 392, 150 262 Z" fill="var(--accent-green)"/>
      <path d="M150 262 C 400 394, 690 428, 1000 416 L1000 420 C 690 434, 400 400, 150 262 Z" fill="var(--divider)"/>
      <path d="M0 197 C 170 300, 430 410, 700 424 C 820 430, 920 426, 1000 422 L1000 571 L0 571 Z" fill="var(--band-dark)"/>
    </svg>

    <h1 class="holder-name">Marcus Bellamy</h1>
    <p class="holder-title">OWNER</p>

    <div class="brand">
      <span class="brand-mark" aria-hidden="true"></span>
      <span class="brand-name">Ridgeline Design + Build</span>
    </div>

    <ul class="contact-list">
      <li class="contact-item">
        <svg class="contact-icon" viewBox="0 0 24 24" aria-hidden="true"><path fill="var(--accent-green)" d="M6.6 10.8a15.2 15.2 0 0 0 6.6 6.6l2.2-2.2c.3-.3.7-.4 1-.2 1.1.4 2.3.6 3.6.6.6 0 1 .4 1 1V20c0 .6-.4 1-1 1C10.6 21 3 13.4 3 4c0-.6.4-1 1-1h3.5c.6 0 1 .4 1 1 0 1.3.2 2.5.6 3.6.1.3 0 .7-.2 1z"/></svg>
        (555) 014-2287
      </li>
      <li class="contact-item">
        <svg class="contact-icon" viewBox="0 0 24 24" aria-hidden="true"><path fill="var(--accent-green)" d="M2 8c0-2 4-4 10-4s10 2 10 4v2h-5V8H7v2H2zM6 12h12l3 8H3zm6 1.5a2.5 2.5 0 1 0 0 5 2.5 2.5 0 0 0 0-5z"/></svg>
        (555) 014-2287
      </li>
      <li class="contact-item">
        <svg class="contact-icon" viewBox="0 0 24 24" aria-hidden="true"><rect x="2.5" y="5" width="19" height="14" rx="1.5" fill="none" stroke="var(--accent-green)" stroke-width="2"/><path d="M3 6l9 7 9-7" fill="none" stroke="var(--accent-green)" stroke-width="2"/></svg>
        ridgeline.build@mail.com
      </li>
      <li class="contact-item">
        <svg class="contact-icon" viewBox="0 0 24 24" aria-hidden="true"><g fill="none" stroke="var(--accent-green)" stroke-width="1.8"><circle cx="12" cy="12" r="9.5"/><ellipse cx="12" cy="12" rx="4.5" ry="9.5"/><path d="M2.5 12h19M4 7h16M4 17h16"/></g></svg>
        <span>www.<span class="contact-highlight">ridgelinebuild</span>.com</span>
      </li>
    </ul>
  </section>
</main>
</body>
</html>
```